Upscale business cards needed for Board of Directors

We need professional business cards created for members of our family business Board of Directors. We would like these relatively simple and straightforward, but also with a unique element to set them apart. Probably stick with neutral and simple colors - white, grey etc. We need space for the traditional elements, including name, title, address, email/phone number. And we will be creating several from this template so it needs to be template that is easy to switch information in and out of.
Business
See description

```html
<!DOCTYPE html>
<html lang="en">
<head>
<meta charset="utf-8">
<title>Harborline Holdings – Business Card</title>
<link rel="stylesheet" href="https://fonts.googleapis.com/css2?family=Open+Sans:wght@400;600;700&display=swap">
<style>
  :root {
    --backdrop: #d8d8d6;
    --card-dark: #2f2e2f;
    --card-light: #ffffff;
    --ink: #1c1c1c;
    --ink-on-dark: #161616;
    --muted: #8a8a8a;
    --muted-dark: #9b9b9b;
    --gold: #a8905f;
  }
  * { box-sizing: border-box; margin: 0; padding: 0; }
  html, body {
    width: 1200px; height: 1000px; overflow: hidden;
    background: var(--backdrop);
    font-family: "Open Sans", sans-serif;
  }
  .canvas { position: relative; width: 1200px; height: 1000px; }

  .card {
    position: absolute; left: 287px; width: 627px; height: 358px;
    box-shadow: 0 6px 14px rgba(0,0,0,0.25);
  }
  .card--back { top: 140px; background: var(--card-dark); }
  .card--front { top: 531px; background: var(--card-light); overflow: hidden; }

  .wordmark {
    position: absolute; text-align: center; font-weight: 700;
    text-transform: uppercase; line-height: 1;
  }
  .wordmark__line1 { display: block; }
  .wordmark__line2 { display: block; }

  .card--back .wordmark {
    left: 0; right: 0; top: 128px; color: var(--ink-on-dark);
  }
  .card--back .wordmark__line1 { font-size: 56px; letter-spacing: 1px; }
  .card--back .wordmark__line2 { font-size: 30px; letter-spacing: 14px; margin-top: 10px; padding-left: 14px; }

  .card--back .website {
    position: absolute; left: 0; right: 0; top: 308px;
    text-align: center; font-size: 14px; color: var(--muted-dark);
  }

  .card--front .wordmark {
    left: 345px; width: 250px; top: 52px; color: var(--ink);
  }
  .card--front .wordmark__line1 { font-size: 35px; letter-spacing: 0.5px; }
  .card--front .wordmark__line2 { font-size: 19px; letter-spacing: 8px; margin-top: 6px; padding-left: 8px; }

  .accent-tab { position: absolute; left: 0; top: 56px; }

  .person { position: absolute; left: 35px; top: 52px; }
  .person__name { font-size: 19px; font-weight: 700; color: var(--gold); line-height: 1.2; }
  .person__title { font-size: 13.5px; color: var(--muted); line-height: 1.3; }

  .contact { position: absolute; left: 35px; top: 251px; list-style: none; }
  .contact li {
    display: flex; align-items: center; gap: 6px;
    font-size: 13.5px; color: var(--muted); height: 18px;
  }
  .contact svg { width: 11px; height: 11px; flex: none; }

  .address {
    position: absolute; right: 35px; top: 251px; text-align: right;
    font-size: 13.5px; color: var(--muted); line-height: 18px;
  }
  .address__label { font-weight: 700; color: var(--gold); }

  .footer-band { position: absolute; left: 0; bottom: 0; }
</style>
</head>
<body>
<main class="canvas">

  <section class="card card--back" aria-label="Card back">
    <div class="wordmark">
      <span class="wordmark__line1">Harborline</span>
      <span class="wordmark__line2">Holdings</span>
    </div>
    <p class="website">www.harborlineholdings.com</p>
  </section>

  <section class="card card--front" aria-label="Card front">
    <svg class="accent-tab" width="24" height="32" viewBox="0 0 24 32" aria-hidden="true">
      <polygon points="0,0 12,0 6,32 0,32" fill="var(--ink)"/>
      <polygon points="15,0 24,0 24,32 9,32" fill="var(--gold)"/>
    </svg>

    <div class="person">
      <p class="person__name">Daniel Moore</p>
      <p class="person__title">President</p>
    </div>

    <div class="wordmark">
      <span class="wordmark__line1">Harborline</span>
      <span class="wordmark__line2">Holdings</span>
    </div>

    <ul class="contact">
      <li>
        <svg viewBox="0 0 12 12" aria-hidden="true"><rect x="3" y="0.5" width="6" height="11" rx="1" fill="none" stroke="var(--muted)" stroke-width="1.2"/><circle cx="6" cy="9.5" r="0.7" fill="var(--muted)"/></svg>
        012-345-6789
      </li>
      <li>
        <svg viewBox="0 0 12 12" aria-hidden="true"><rect x="0.5" y="2.5" width="11" height="7" fill="var(--muted)"/><polyline points="0.5,2.5 6,6.5 11.5,2.5" fill="none" stroke="#fff" stroke-width="1"/></svg>
        info@harborlineholdings.com
      </li>
      <li>
        <svg viewBox="0 0 12 12" aria-hidden="true"><circle cx="6" cy="6" r="5" fill="var(--muted)"/><ellipse cx="6" cy="6" rx="2" ry="5" fill="none" stroke="#fff" stroke-width="0.8"/><line x1="1" y1="6" x2="11" y2="6" stroke="#fff" stroke-width="0.8"/></svg>
        www.harborlineholdings.com
      </li>
    </ul>

    <address class="address" style="font-style:normal">
      <span class="address__label">Address</span><br>
      Street name, Suite 100 State,<br>
      Zip Code, Country
    </address>

    <svg class="footer-band" width="627" height="24" viewBox="0 0 627 24" aria-hidden="true">
      <polygon points="0,11 304,11 297,24 0,24" fill="var(--ink)"/>
      <polygon points="324,0 627,0 627,24 293,24" fill="var(--gold)"/>
    </svg>
  </section>

</main>
</body>
</html>
```